App-Design für Vergleichsportal für Reparaturen
Zielgruppe
Flickwerkzentrale ist das Vergleichsportal für Reparaturen in deiner Nähe. Egal ob du eine Werkstatt für dein Smartphone, Tablet, Laptop, Computer, Smartwatch oder Spielkonsole suchst. Mit uns findest du deine passende Reparaturwerkstat in deiner Nähe mit dem besten Preis für dich. Du kannst dich direkt über unser Portal deinen Reparaturauftrag erhalten und wirst durch unser Sicher Kaufen Käuferschutz und unser VORMANT Treuhandschutz abgesichert.
Aufgabenstellung
Unter Flickwerkzentrale.de kann das aktuelle Design angeschaut werden. Die Farbe sollten übernommen werden.
Über die Startseite kann der Kunde sein Gerät, Service sowie seine Adresse eingeben. Auf der Vergleichsseite bekommt der Kunde die Übersicht welche Reparaturwerkstätten es gibt, zu welche Preisen die ausgewählte Dienstleistung angeboten wird. Wenn der Kunde auf den Button 'Jetzt Online Bestpreis buchen' drückt, dann kommt der Kunde in den Warenkorb. Im Warenkorb können noch weitere Dienstleistungen und Produkte dazugebucht werden. Und anschließend kommt der Kunde in die Kasse und kann der Bestellvorgang beenden. Die Benutzerführung sollte einfach sein. Im Fokus steht die Vergleichsseite. Dort sollte der Kunde ca. 4 Werkstätten auf einen Blick sehen können. Könnte ausschauen wie bei Tarifblick in der Kategorie Mobilfunk.
Die Vergleichseite sollte auf jeden Fall folgende Elemente enthalten:
- Entfernung zur Werkstatt in Meter bzw. Kilometer
- Logo der Werkstatt
- Name der Werkstatt
- Bewertungssterne der Werkstatt
- Reparaturzeit und Ersatzeilverfügbarkeit
- Reparaturpreis (Platz sollte auch bei Auswahl von 2 Dienstleistungen vorhanden sein)
- Rabattanzeige
- Qualitätssiegel (noch nicht vorhanden)
- Anzeige von Verknappung (z. B. noch 3 Termin frei)
- Qualitätsmerkmale (z. B. 12 Monate Garantie)
Die Merkmale Öffnungszeiten, Adresse, Kostenpflichtige Zusatzleistungen können aus Platzgründen in den Warenkorbseite wandern außer es gibt eine schöne und einfache Lösung.
In der Warenkorbseite kann dazu auch die Tarifblick Seite dienen.
Bei allen sollte auf die Benutzerfreundlichkeit geachtet werden.
Bei offenen Frage stehe ich zur Verfügung und freue mich auf viele Designs.
Vielen DANK im Voraus!

```html
<!DOCTYPE html>
<html lang="de">
<head>
<meta charset="utf-8">
<title>Flickwerkzentrale – Vergleich</title>
<link href="https://fonts.googleapis.com/css2?family=Source+Sans+3:wght@300;400;600;700&display=swap" rel="stylesheet">
<style>
:root{
  --stage:#262626;
  --teal:#1f4a5c;
  --lime:#8dc63f;
  --star:#d4dc00;
  --ink:#2e3a40;
  --red:#e0102a;
  --orange:#e8702a;
  --brandred:#d7192a;
  --page:#eef0f2;
  --card:#ffffff;
  --line:#c9cfd2;
}
*{box-sizing:border-box;margin:0;padding:0}
html,body{width:1200px;height:728px;overflow:hidden;background:var(--stage);font-family:"Source Sans 3",sans-serif;color:var(--ink)}
.screen{position:absolute;left:432px;top:0;width:336px;height:728px;background:var(--page);overflow:hidden}
.status{height:34px;background:#fff;display:flex;align-items:center;justify-content:space-between;padding:0 14px 0 16px;font-weight:600;font-size:12px;color:#333}
.status svg{display:block}
.topbar{height:54px;background:#fff;display:flex;align-items:center;justify-content:space-between;padding:0 14px}
.brand{display:flex;align-items:center;gap:6px;font-size:14px;font-weight:600;color:var(--teal)}
.brand i{width:12px;height:12px;border-radius:50%;background:var(--lime);display:block}
.menu{width:20px;display:flex;flex-direction:column;gap:5px}
.menu span{height:1.5px;background:var(--teal)}
.hero{height:73px;background:var(--teal);text-align:center;padding-top:22px}
.hero h1{font-size:11px;font-weight:700;color:var(--lime)}
.hero p{font-size:9px;color:var(--lime);margin-top:3px}
.list{padding:18px 26px 0}
.offer{background:var(--card);padding:9px 9px 11px;margin-bottom:11px}
.head{display:flex;justify-content:space-between;align-items:flex-start}
.shop{font-size:12.5px;font-weight:300;color:var(--ink);white-space:nowrap}
.logo{display:flex;align-items:center;gap:5px;margin-top:4px;font-size:17px;font-weight:600;color:var(--teal);height:22px}
.logo i{width:16px;height:16px;background:var(--teal);display:block}
.logo.orange{color:var(--orange)}
.logo.orange i{background:var(--orange);border-radius:50%}
.logo.red{color:var(--brandred)}
.logo.red i{background:var(--brandred)}
.prices{text-align:right}
.old{font-size:14px;text-decoration:line-through;color:var(--ink);margin-top:6px}
.now{font-size:18px;color:var(--lime);line-height:1.1}
.now.solo{margin-top:10px}
.stars{display:flex;gap:2px;margin-top:4px}
.stars svg{width:10px;height:10px;fill:var(--star)}
.facts{display:flex;margin-top:8px;font-size:8px;line-height:1.35}
.where{width:96px;border-right:1px solid var(--line);padding-right:6px}
.where .row{display:flex;gap:4px;align-items:flex-start}
.where svg{flex:none;margin-top:1px}
.km{margin-top:5px}
.specs{flex:1;padding-left:11px;display:flex;justify-content:space-between}
.specs .val{text-align:right;color:var(--lime)}
.specs .val .no{color:var(--red)}
.badges{display:flex;justify-content:space-between;margin-top:10px}
.badge{width:82px;height:25px;border:1.5px solid var(--teal);display:flex;align-items:center}
.badge .ico{width:23px;height:100%;background:var(--teal);display:flex;align-items:center;justify-content:center}
.badge .txt{flex:1;text-align:center;font-size:6.5px;color:var(--lime);line-height:1.1}
.badge .txt.no{color:var(--red)}
.book{margin-top:12px;height:29px;background:var(--lime);color:#fff;font-size:10.5px;display:flex;align-items:center;justify-content:center;gap:7px}
</style>
</head>
<body>
<svg width="0" height="0" style="position:absolute">
  <defs>
    <symbol id="star" viewBox="0 0 10 10"><path d="M5 0l1.5 3.3 3.5.3-2.7 2.3.8 3.5L5 7.6 1.9 9.4l.8-3.5L0 3.6l3.5-.3z"/></symbol>
    <symbol id="pin" viewBox="0 0 7 10"><path d="M3.5 0A3.5 3.5 0 0 0 0 3.5C0 6 3.5 10 3.5 10S7 6 7 3.5A3.5 3.5 0 0 0 3.5 0z" fill="#8dc63f"/><circle cx="3.5" cy="3.5" r="1.3" fill="#fff"/></symbol>
    <symbol id="route" viewBox="0 0 9 9"><path d="M1 8h7M2 8V5h3V2h3" stroke="#8dc63f" stroke-width="1.2" fill="none"/></symbol>
    <symbol id="truck" viewBox="0 0 14 10"><path d="M1 1h8v6H1zM9 3h3l1.5 2v2H9" stroke="#8dc63f" fill="none"/><circle cx="3.5" cy="8" r="1.2" fill="#8dc63f"/><circle cx="11" cy="8" r="1.2" fill="#8dc63f"/></symbol>
    <symbol id="thumb" viewBox="0 0 12 12"><path d="M1 6h2v5H1zM3 6l3-5 1 1-1 3h4.5l-1 6H3" stroke="#8dc63f" fill="none"/></symbol>
    <symbol id="seal" viewBox="0 0 12 12"><circle cx="6" cy="6" r="5" stroke="#8dc63f" fill="none"/></symbol>
    <symbol id="cart" viewBox="0 0 14 12"><path d="M0 1h2.5l2 7h7l1.5-5H4" stroke="#fff" stroke-width="1.2" fill="none"/><circle cx="5.5" cy="10.5" r="1" fill="#fff"/><circle cx="10.5" cy="10.5" r="1" fill="#fff"/></symbol>
  </defs>
</svg>
<main class="screen">
  <div class="status">
    <span>9:41</span>
    <svg width="52" height="10" viewBox="0 0 52 10"><rect x="0" y="7" width="2" height="3" fill="#333"/><rect x="3" y="5" width="2" height="5" fill="#333"/><rect x="6" y="3" width="2" height="7" fill="#333"/><rect x="9" y="1" width="2" height="9" fill="#333"/><path d="M17 4a8 8 0 0 1 10 0M19 6.5a5 5 0 0 1 6 0" stroke="#333" stroke-width="1.5" fill="none"/><circle cx="22" cy="9" r="1" fill="#333"/><rect x="32" y="1" width="17" height="8" rx="2" stroke="#333" fill="none"/><rect x="34" y="3" width="13" height="4" fill="#333"/></svg>
  </div>
  <header class="topbar">
    <div class="brand"><i></i>Flickwerkzentrale</div>
    <div class="menu"><span></span><span></span><span></span></div>
  </header>
  <section class="hero">
    <h1>Reparaturen Im Vergleich, in deiner Nähe!</h1>
    <p>Garantiert die besten Tarife</p>
  </section>

  <section class="list">
    <article class="offer">
      <div class="head">
        <div>
          <div class="shop">Kantel Repair Lindbach</div>
          <div class="logo"><i></i>KANTELREPAIR</div>
          <div class="stars"><svg><use href="#star"/></svg><svg><use href="#star"/></svg><svg><use href="#star"/></svg><svg><use href="#star"/></svg><svg><use href="#star"/></svg></div>
        </div>
        <div class="prices"><div class="old">87,00€</div><div class="now">79,00€</div></div>
      </div>
      <div class="facts">
        <div class="where">
          <div class="row"><svg width="7" height="10"><use href="#pin"/></svg><span>Lindenweg 7<br>41207 Lindbach</span></div>
          <div class="row km"><svg width="9" height="9"><use href="#route"/></svg><span>19 km</span></div>
        </div>
        <div class="specs"><div>Reparaturzeit:<br>Ersatzteilverfügbarkeit:<br>Verknappung:</div><div class="val">2 Tage<br>Verfügbar<br>noch 3 Termine frei</div></div>
      </div>
      <div class="badges">
        <div class="badge"><div class="ico"><svg width="14" height="10"><use href="#truck"/></svg></div><div class="txt">Versand möglich</div></div>
        <div class="badge"><div class="ico"><svg width="12" height="12"><use href="#thumb"/></svg></div><div class="txt">12 Monate Garantie</div></div>
        <div class="badge"><div class="ico"><svg width="12" height="12"><use href="#seal"/></svg></div><div class="txt">Muster Siegel</div></div>
      </div>
      <div class="book"><svg width="14" height="12"><use href="#cart"/></svg>Jetzt Online Bestpreis buchen</div>
    </article>

    <article class="offer">
      <div class="head">
        <div>
          <div class="shop">Handyhaus Lindbach Oststadt</div>
          <div class="logo orange"><i></i>Handyhaus</div>
          <div class="stars"><svg><use href="#star"/></svg><svg><use href="#star"/></svg><svg><use href="#star"/></svg><svg><use href="#star"/></svg><svg><use href="#star"/></svg></div>
        </div>
        <div class="prices"><div class="now solo">79,00€</div></div>
      </div>
      <div class="facts">
        <div class="where">
          <div class="row"><svg width="7" height="10"><use href="#pin"/></svg><span>Ahornstraße 52b<br>41215 Lindbach</span></div>
          <div class="row km"><svg width="9" height="9"><use href="#route"/></svg><span>19 km</span></div>
        </div>
        <div class="specs"><div>Reparaturzeit:<br>Ersatzteilverfügbarkeit:<br>Verknappung:</div><div class="val">2 Tage<br><span class="no">nicht verfügbar</span><br>noch 3 Termine frei</div></div>
      </div>
      <div class="badges">
        <div class="badge"><div class="ico"><svg width="14" height="10"><use href="#truck"/></svg></div><div class="txt no">Versand nicht möglich</div></div>
        <div class="badge"><div class="ico"><svg width="12" height="12"><use href="#thumb"/></svg></div><div class="txt">12 Monate Garantie</div></div>
        <div class="badge"><div class="ico"><svg width="12" height="12"><use href="#seal"/></svg></div><div class="txt">Muster Siegel</div></div>
      </div>
      <div class="book"><svg width="14" height="12"><use href="#cart"/></svg>Jetzt Online Bestpreis buchen</div>
    </article>

    <article class="offer">
      <div class="head">
        <div>
          <div class="shop">Zellwerk am Marktplatz</div>
          <div class="logo red"><i></i>Zellwerk</div>
          <div class="stars"><svg><use href="#star"/></svg><svg><use href="#star"/></svg><svg><use href="#star"/></svg><svg><use href="#star"/></svg><svg><use href="#star"/></svg></div>
        </div>
        <div class="prices"><div class="old">100,00€</div><div class="now">89,00€</div></div>
      </div>
      <div class="facts">
        <div class="where">
          <div class="row"><svg width="7" height="10"><use href="#pin"/></svg><span>Birkenstr 14<br>41221 Lindbach</span></div>
          <div class="row km"><svg width="9" height="9"><use href="#route"/></svg><span>19 km</span></div>
        </div>
        <div class="specs"><div>Reparaturzeit:<br>Ersatzteilverfügbarkeit:<br>Verknappung:</div><div class="val">2 Tage<br>Verfügbar<br>noch 3 Termine frei</div></div>
      </div>
    </article>
  </section>
</main>
</body>
</html>
```